Business Card- Can you make it cool vs boring!

Need a refresh on my business card! Want it to be modern but simple, classic and a pop of coolness! we do senior living and it is boring. but that doesn't mean our business card have to look boring! Open to two sided cards. our website is www.Dunmere-PK.com

Target Market(s)

capital market

Industry/Entity Type

senior housing/ real estate

Contact Information for Business Card

logo/ name/ cell/ address/ www.Dunmere-PK.com/ space for a QR code

Requirements
Must have
• maybe a QR code (do not make prominent I may not use the QR so design where it can be taken out) that link to more about us/ landing page. needs to be modern but clean
Should not have
• clip art or script

```html
<!DOCTYPE html>
<html lang="en">
<head>
<meta charset="utf-8">
<title>Dunmere Living – Business Card</title>
<link href="https://fonts.googleapis.com/css2?family=Poppins:wght@400;500;700&display=swap" rel="stylesheet">
<style>
  :root{
    --bg-dark:#141414;
    --bg-mid:#2b2b2b;
    --card:#0d0d0d;
    --card-edge:#1a1a1a;
    --accent:#b9531f;
    --text-light:#d9d9d9;
    --text-muted:#9a9a9a;
    --silver:#d4d4d4;
    --rule:#555555;
  }
  *{margin:0;padding:0;box-sizing:border-box}
  html,body{width:1200px;height:900px;overflow:hidden}
  body{
    background:radial-gradient(ellipse at 50% 40%,var(--bg-mid) 0%,var(--bg-dark) 75%);
    font-family:"Poppins",sans-serif;
    display:flex;align-items:center;justify-content:center;gap:40px;
  }
  .card{
    width:540px;height:309px;border-radius:18px;
    background:linear-gradient(160deg,var(--card-edge) 0%,var(--card) 55%);
    border-bottom:6px solid var(--accent);
    box-shadow:0 20px 40px rgba(0,0,0,.6);
    position:relative;overflow:hidden;
  }
  /* front */
  .card-front{display:flex;align-items:center}
  .brand-block{width:48%;display:flex;align-items:center;justify-content:center;padding-top:40px}
  .brand-name{font-weight:500;font-size:30px;color:var(--accent);letter-spacing:.5px;white-space:nowrap}
  .divider{width:1px;height:170px;background:var(--rule)}
  .contact-block{padding-left:26px;color:var(--text-light);font-size:13px;line-height:1.45}
  .person-name{font-weight:700;font-size:18px;color:var(--accent);letter-spacing:.5px;line-height:1.1}
  .person-title{font-size:13px;color:var(--text-light);margin-bottom:12px}
  .contact-list{list-style:none}
  .contact-item{display:flex;align-items:center;gap:8px}
  .contact-item svg{width:13px;height:13px;flex:none}
  .web-highlight{color:var(--accent)}
  .address{margin-top:10px;padding-left:21px}
  /* back */
  .card-back{display:flex;align-items:center;justify-content:center}
  .card-back .brand-name{color:var(--silver);font-size:40px}
</style>
</head>
<body>
  <section class="card card-front" aria-label="Business card front">
    <div class="brand-block"><span class="brand-name">Dunmere Living</span></div>
    <div class="divider"></div>
    <div class="contact-block">
      <p class="person-name">MARCUS HALE</p>
      <p class="person-title">Managing Director</p>
      <ul class="contact-list">
        <li class="contact-item">
          <svg viewBox="0 0 24 24" fill="var(--accent)"><path d="M6.6 10.8a15 15 0 0 0 6.6 6.6l2.2-2.2c.3-.3.7-.4 1-.2 1.1.4 2.3.6 3.6.6.6 0 1 .4 1 1V20c0 .6-.4 1-1 1A17 17 0 0 1 3 4c0-.6.4-1 1-1h3.5c.6 0 1 .4 1 1 0 1.3.2 2.5.6 3.6.1.3 0 .7-.2 1z"/></svg>
          044-555 210 384
        </li>
        <li class="contact-item">
          <svg viewBox="0 0 24 24" fill="var(--accent)"><path d="M2 5h20v14H2z" opacity="1"/><path d="M2 5l10 8 10-8" fill="none" stroke="var(--card)" stroke-width="2"/></svg>
          info@dunmere-pk.com
        </li>
        <li class="contact-item">
          <svg viewBox="0 0 24 24" fill="none" stroke="var(--accent)" stroke-width="2"><circle cx="12" cy="12" r="10"/><path d="M2 12h20M12 2c3 3 3 17 0 20M12 2c-3 3-3 17 0 20"/></svg>
          <span>www.<span class="web-highlight">Dunmere-PK</span>.com</span>
        </li>
      </ul>
      <p class="address">421, Address line goes here<br>45452,Country Name</p>
    </div>
  </section>

  <section class="card card-back" aria-label="Business card back">
    <span class="brand-name">Dunmere Living</span>
  </section>
</body>
</html>
```